Our Company is Harbourline Lot Planners and we service the whole Perth Metro region. We want our flyer to grab the potential clients attention and inform them of their potential opportunity to subdivide their residential property. We would like the flyer to show our logo, contact details website and maybe one eye catching, engaging picture/photo. If the Flyer could follow the same colours as our logo that would be great. Are we able to have a A5 size flyer front and back? maybe our contact information on the back? and other services that we offer?
A lot of our potential clients aren't aware their house/land is sub dividable, or even know how to do a subdivision. We would like our flyer to educate the average residential home owner of the potential of their property and make the idea of subdividing seem and easy and accessible. Something along the lines of "Looking to Subdivide? Not sure if your property is sub-dividable? Call us now for a obligation free assessment of your property." or maybe "Subdividing you property is easier than you might think..."
We would like to advertise that we offer:-
Free Subdivision feasibility analysis of your property,
Project Management: We offer full Project Management from start to finish ensuring a hassle free subdivision (or something along those lines)-
New title's application
Updates

Target Market(s)

Residential Home owners with the potential to subdivide their property.

Industry/Entity Type

Surveyor

Colors
f78f20
c3c3c3
3176b5

Requirements
Must have
• Simple, clutter free design offering the idea of subdividing as a new, accessible opportunity to the average homeowner.

```html
<!DOCTYPE html>
<html lang="en">
<head>
<meta charset="utf-8">
<title>Harbourline Lot Planners – Subdivision Flyer</title>
<link rel="stylesheet" href="https://fonts.googleapis.com/css2?family=Oswald:wght@500;600&family=Lato:wght@400;700&family=Montserrat:wght@800&family=Roboto:wght@400&display=swap">
<style>
  :root{
    --orange:#f26a23;
    --orange-light:#f78f20;
    --blue:#1f63b3;
    --blue-light:#3176b5;
    --navy:#142a43;
    --grey:#c3c3c3;
    --dark:#3a3a3a;
    --text:#2b2b2b;
    --white:#ffffff;
    --backdrop:#8d8d8d;
  }
  *{margin:0;padding:0;box-sizing:border-box}
  html,body{width:900px;height:1200px;overflow:hidden}
  body{background:var(--backdrop);position:relative;font-family:'Lato',sans-serif}
  .flyer{position:absolute;left:92px;top:95px;width:716px;height:1010px;background:var(--white);overflow:hidden}
  .flyer-shapes{position:absolute;left:0;top:0}
  .hero-photo{position:absolute;left:0;top:0;width:716px;height:400px}
  .headline{position:absolute;left:18px;top:22px;width:240px;text-align:center;color:var(--white)}
  .headline .big{font-family:'Oswald',sans-serif;font-weight:600;font-size:46px;line-height:1;letter-spacing:.5px}
  .headline .sub{font-family:'Roboto',sans-serif;font-size:28px;color:#1d1d1d;line-height:1.1}
  .headline .small{font-family:'Roboto',sans-serif;font-size:21px;color:#1d1d1d;line-height:1.1}
  .headline .mid{font-family:'Oswald',sans-serif;font-weight:600;font-size:26px;line-height:1.2}
  .headline .gap{height:20px}
  .brand{position:absolute;left:0;top:430px;width:716px;text-align:center}
  .brand-mark{width:14px;height:14px;border-radius:50%;background:var(--navy);margin:0 auto 16px}
  .brand-name{font-family:'Lato',sans-serif;font-weight:700;font-size:44px;color:var(--navy);line-height:1.1}
  .pill{position:absolute;left:0;color:var(--white);display:flex;align-items:center;border-radius:0 40px 40px 0;box-shadow:0 6px 8px rgba(0,0,0,.2)}
  .pill-offer{top:550px;width:276px;height:67px;background:linear-gradient(90deg,var(--blue),var(--blue-light));font-family:'Montserrat',sans-serif;font-weight:800;font-size:34px;padding-left:28px;letter-spacing:1px}
  .pill-pm{top:763px;width:300px;height:44px;background:linear-gradient(90deg,var(--blue),var(--blue-light));font-family:'Oswald',sans-serif;font-weight:500;font-size:23px;padding-left:26px}
  .offer-title{position:absolute;left:26px;top:645px;font-family:'Lato',sans-serif;font-size:48px;color:var(--text);line-height:1}
  .offer-title strong{font-weight:700}
  .offer-sub{position:absolute;left:26px;top:697px;font-family:'Roboto',sans-serif;font-size:23px;color:var(--text)}
  .pm-text{position:absolute;left:26px;top:832px;width:320px;font-size:18px;line-height:1.35;color:var(--text);text-align:justify}
  .services-tab{position:absolute;left:437px;top:693px;width:187px;height:42px;background:var(--orange);color:var(--white);font-family:'Oswald',sans-serif;font-weight:500;font-size:24px;display:flex;align-items:center;padding-left:34px;border-radius:0 24px 24px 0}
  .services-list{position:absolute;left:472px;top:756px;list-style:none;color:var(--white);font-weight:700;font-size:18.5px;line-height:24px}
  .services-list li{position:relative;padding-left:18px}
  .services-list li::before{content:"";position:absolute;left:0;top:9px;width:8px;height:8px;border-radius:50%;background:var(--orange)}
  .footer{position:absolute;left:0;top:937px;width:716px;height:73px;background:var(--blue);color:var(--white);font-weight:700;font-size:16px}
  .contact{position:absolute;display:flex;align-items:center;gap:12px}
  .contact svg{width:14px;height:14px;flex:none}
</style>
</head>
<body>
  <main class="flyer">
    <div class="hero-photo" role="img" aria-label="Photo of a city skyline across a river with a surveying total station in the foreground" style="background:linear-gradient(180deg,#dfe2e6 0%,#c9ccd0 42%,#6f7a86 55%,#9aa2aa 75%,#b3b8bd 100%)"></div>

    <svg class="flyer-shapes" width="716" height="1010" viewBox="0 0 716 1010">
      <defs>
        <linearGradient id="orangeFade" x1="0" y1="0" x2="0" y2="1">
          <stop offset="0" stop-color="#f26a23"/>
          <stop offset="1" stop-color="#f78f20"/>
        </linearGradient>
        <radialGradient id="darkPanel" cx="0.75" cy="0.3" r="0.9">
          <stop offset="0" stop-color="#6b6b6b"/>
          <stop offset="1" stop-color="#2e2e2e"/>
        </radialGradient>
      </defs>
      <!-- orange headline panel -->
      <path d="M0,0 L300,0 C288,110 300,220 262,300 Q150,330 0,385 Z" fill="url(#orangeFade)"/>
      <path d="M300,0 C288,110 300,220 262,300" fill="none" stroke="var(--blue)" stroke-width="8"/>
      <!-- white body below arc -->
      <path d="M0,390 Q330,240 716,372 L716,1010 L0,1010 Z" fill="#ffffff"/>
      <path d="M0,380 Q330,232 716,362" fill="none" stroke="var(--blue)" stroke-width="16"/>
      <path d="M0,392 Q330,246 716,374" fill="none" stroke="var(--orange)" stroke-width="4"/>
      <!-- dark services panel -->
      <path d="M398,937 C408,780 510,620 716,578 L716,937 Z" fill="url(#darkPanel)"/>
      <path d="M378,937 C388,770 500,605 716,566" fill="none" stroke="var(--blue)" stroke-width="7"/>
      <path d="M390,937 C400,776 505,613 716,573" fill="none" stroke="var(--orange)" stroke-width="4"/>
    </svg>

    <header class="headline">
      <div class="big">LOOKING TO</div>
      <div class="sub">SUBDIVIDE ?</div>
      <div class="gap"></div>
      <div class="big">NOT SURE</div>
      <div class="small">IF YOUR PROPERTY</div>
      <div class="mid">IS SUBDIVIDABLE ?</div>
    </header>

    <div class="brand">
      <div class="brand-mark"></div>
      <div class="brand-name">Harbourline Lot Planners</div>
    </div>

    <div class="pill pill-offer">WE OFFER</div>
    <h1 class="offer-title"><strong>Free</strong> Subdivision</h1>
    <p class="offer-sub">feasibility analysis of your property</p>

    <div class="pill pill-pm">PROJECT MANAGEMENT</div>
    <p class="pm-text">We offer full Project Management from start to finish ensuring a hassle free subdivision.</p>

    <div class="services-tab">SERVICES</div>
    <ul class="services-list">
      <li>Consultancy</li>
      <li>Planning Application</li>
      <li>Survey Work &amp; Project<br>Management</li>
      <li>Application for<br>new titles</li>
    </ul>

    <footer class="footer">
      <div class="contact" style="left:26px;top:10px">
        <svg viewBox="0 0 24 24"><path d="M6.6 10.8a15 15 0 0 0 6.6 6.6l2.2-2.2a1 1 0 0 1 1-.25 11.4 11.4 0 0 0 3.6.57 1 1 0 0 1 1 1V20a1 1 0 0 1-1 1A17 17 0 0 1 3 4a1 1 0 0 1 1-1h3.5a1 1 0 0 1 1 1c0 1.25.2 2.45.57 3.57a1 1 0 0 1-.25 1z" fill="var(--orange-light)"/></svg>
        <span>(08) 9410 2285</span>
      </div>
      <div class="contact" style="left:26px;top:38px">
        <svg viewBox="0 0 24 24"><rect x="2" y="5" width="20" height="14" fill="var(--orange-light)"/><path d="M2 5l10 8 10-8" fill="none" stroke="var(--blue)" stroke-width="2"/></svg>
        <span>info@harbourlinelots.com</span>
      </div>
      <div class="contact" style="left:332px;top:10px">
        <svg viewBox="0 0 24 24"><circle cx="12" cy="12" r="10" fill="none" stroke="var(--orange-light)" stroke-width="2"/><path d="M2 12h20M12 2c3 3 3 17 0 20M12 2c-3 3-3 17 0 20" fill="none" stroke="var(--orange-light)" stroke-width="1.6"/></svg>
        <span>www.harbourlinelots.com</span>
      </div>
      <div class="contact" style="left:332px;top:38px">
        <svg viewBox="0 0 24 24"><path d="M12 2a7 7 0 0 0-7 7c0 5 7 13 7 13s7-8 7-13a7 7 0 0 0-7-7zm0 9.5A2.5 2.5 0 1 1 12 6.5a2.5 2.5 0 0 1 0 5z" fill="var(--orange-light)"/></svg>
        <span>P.O Box 318 Harbourline, WA. 6000</span>
      </div>
    </footer>
  </main>
</body>
</html>
```